" Venda de planos de assistência familiar oferecendo uma rede descontos e funerais para os seus associados ; Serviços funerários; Venda de coroa de flores e arranjos. "

```html
<!DOCTYPE html>
<html lang="pt-BR">
<head>
<meta charset="utf-8">
<title>Laço Sereno – Papel Timbrado</title>
<link rel="stylesheet" href="https://fonts.googleapis.com/css2?family=Montserrat:wght@400;500;700&display=swap">
<style>
  :root {
    --backdrop: #e9e6e2;
    --paper: #ffffff;
    --teal: #19a3a0;
    --teal-soft: #8fcfcd;
    --ink: #1f5f62;
    --text: #2c3e40;
    --watermark: #ececec;
  }
  * { margin: 0; padding: 0; box-sizing: border-box; }
  html, body { width: 1200px; height: 1200px; overflow: hidden; }
  body {
    background: var(--backdrop);
    font-family: "Montserrat", sans-serif;
    position: relative;
  }
  .letterhead {
    position: absolute;
    left: 235px; top: 50px;
    width: 730px; height: 1100px;
    background: var(--paper);
    box-shadow: 0 6px 24px rgba(0,0,0,0.18);
  }
  .brand {
    position: absolute;
    left: 22px; top: 46px;
    display: flex; align-items: center; gap: 12px;
  }
  .brand-dot {
    width: 34px; height: 34px; border-radius: 50%;
    background: var(--teal);
  }
  .brand-text { display: flex; flex-direction: column; }
  .brand-name {
    font-weight: 700; font-size: 25px; letter-spacing: 0.5px;
    color: var(--ink); line-height: 1;
  }
  .brand-tagline {
    font-weight: 400; font-size: 8.5px; letter-spacing: 0.6px;
    color: var(--teal); margin-top: 4px; text-transform: uppercase;
  }
  .rule {
    position: absolute; left: 15px; right: 20px;
    height: 2px; background: var(--teal-soft);
  }
  .rule-accent {
    position: absolute; top: -2px; height: 6px; background: var(--teal);
  }
  .rule-header { top: 121px; }
  .rule-header .rule-accent { left: 0; width: 204px; }
  .rule-footer { top: 1016px; }
  .rule-footer .rule-accent { right: 0; width: 154px; }
  .watermark {
    position: absolute;
    left: 132px; top: 300px;
    width: 440px; height: 440px;
    border-radius: 50%;
    background: var(--watermark);
    opacity: 0.7;
  }
  .contacts {
    position: absolute; left: 22px; right: 20px; top: 1036px;
    display: flex; align-items: center; justify-content: space-between;
    font-size: 15px; font-weight: 500; color: var(--text);
  }
  .contact { display: flex; align-items: center; gap: 10px; }
  .contact svg { width: 22px; height: 22px; flex: none; }
  .contact-social-dot {
    width: 18px; height: 18px; border-radius: 50%;
    border: 2px solid var(--teal);
  }
</style>
</head>
<body>
  <main class="letterhead">
    <header class="brand">
      <span class="brand-dot"></span>
      <div class="brand-text">
        <span class="brand-name">LAÇO SERENO</span>
        <span class="brand-tagline">plano de assistência familiar</span>
      </div>
    </header>
    <div class="rule rule-header"><span class="rule-accent"></span></div>

    <div class="watermark" role="img" aria-label="Marca da empresa em tom claro ao fundo da folha"></div>

    <div class="rule rule-footer"><span class="rule-accent"></span></div>
    <footer class="contacts">
      <div class="contact">
        <svg viewBox="0 0 24 24" fill="none" stroke="var(--teal)" stroke-width="2" stroke-linecap="round" stroke-linejoin="round">
          <path d="M5 3h4l2 5-2.5 1.5a11 11 0 0 0 6 6L16 13l5 2v4a2 2 0 0 1-2 2A16 16 0 0 1 3 5a2 2 0 0 1 2-2z"/>
        </svg>
        <span>00 0000-0000 | 00 00000-0000</span>
      </div>
      <div class="contact">
        <svg viewBox="0 0 24 24" fill="none" stroke="var(--teal)" stroke-width="1.8" stroke-linejoin="round">
          <rect x="2.5" y="5" width="19" height="14"/>
          <path d="M2.5 5l9.5 8 9.5-8M2.5 19l7-6.5M21.5 19l-7-6.5"/>
        </svg>
        <span>seuemail@seuemail.com.br</span>
      </div>
      <div class="contact">
        <span class="contact-social-dot"></span>
        <span>lacosereno</span>
      </div>
    </footer>
  </main>
</body>
</html>
```